Business card for event manager / organizer "waiter service"

Draft of a new valuable business card for my company.
Events, personnel service providers, festivals

```html
<!DOCTYPE html>
<html lang="de">
<head>
<meta charset="utf-8">
<title>Bergers Kellnerservice – Visitenkarte</title>
<link href="https://fonts.googleapis.com/css2?family=Poppins:wght@300;400;600;700&family=Exo+2:wght@300&display=swap" rel="stylesheet">
<style>
  :root {
    --page-bg: #d9d9db;
    --card-bg: #252326;
    --orange: #ef7d1e;
    --white: #ffffff;
    --muted: #e6e6e6;
    --photo-light: #c9c9cc;
    --photo-dark: #2b292c;
  }
  * { margin: 0; padding: 0; box-sizing: border-box; }
  html, body { width: 1200px; height: 900px; overflow: hidden; }
  body {
    background: var(--page-bg);
    font-family: "Poppins", sans-serif;
    position: relative;
  }
  .card {
    position: absolute;
    left: 250px;
    width: 700px;
    height: 400px;
    background: var(--card-bg);
    border-radius: 22px;
    overflow: hidden;
    box-shadow: 0 10px 30px rgba(0,0,0,.25);
  }
  .card--front { top: 25px; }
  .card--back { top: 475px; }

  /* Brand lockup */
  .brand { display: flex; align-items: center; }
  .brand__mark { background: var(--orange); flex: none; }
  .brand__name {
    font-weight: 700;
    color: var(--white);
    text-transform: uppercase;
    line-height: 1.05;
    letter-spacing: .5px;
  }
  .brand__tagline {
    font-family: "Exo 2", sans-serif;
    font-weight: 300;
    color: var(--white);
    white-space: nowrap;
  }

  .card--front .brand {
    position: absolute;
    left: 120px; top: 130px;
    gap: 28px;
  }
  .card--front .brand__mark { width: 110px; height: 110px; border-radius: 14px; }
  .card--front .brand__name { font-size: 48px; }
  .card--front .brand__tagline {
    position: absolute;
    left: 258px; top: 262px;
    font-size: 20px;
  }

  .card--back .brand {
    position: absolute;
    left: 40px; top: 34px;
    gap: 12px;
  }
  .card--back .brand__mark { width: 48px; height: 48px; border-radius: 7px; }
  .card--back .brand__name { font-size: 19px; }
  .card--back .brand__tagline {
    position: absolute;
    left: 100px; top: 86px;
    font-size: 9px;
  }

  .photo {
    position: absolute;
    right: 0; top: 0;
    width: 270px; height: 400px;
    background: radial-gradient(ellipse at 55% 40%, var(--photo-light) 0%, #8d8c90 45%, var(--photo-dark) 85%);
  }

  .person { position: absolute; left: 72px; top: 128px; }
  .person__name { font-size: 32px; font-weight: 600; color: var(--orange); line-height: 1.1; }
  .person__role { font-size: 17px; font-weight: 300; color: var(--muted); margin-top: 2px; margin-left: 10px; }

  .contact-list {
    position: absolute;
    left: 80px; top: 220px;
    list-style: none;
  }
  .contact-list__item {
    display: flex; align-items: center; gap: 12px;
    font-size: 16px; font-weight: 400; color: var(--white);
    height: 25px;
    white-space: nowrap;
  }
  .contact-list__icon { width: 15px; height: 15px; flex: none; fill: var(--orange); }
</style>
</head>
<body>

<section class="card card--front" aria-label="Vorderseite">
  <div class="brand">
    <span class="brand__mark"></span>
    <span class="brand__name">Bergers<br>Kellnerservice</span>
  </div>
  <p class="brand__tagline">…damit Ihre Gäste bestens versorgt sind!</p>
</section>

<section class="card card--back" aria-label="Rückseite">
  <div class="photo" role="img" aria-label="Porträtfoto des Inhabers in Weste und weißem Hemd mit verschränkten Armen"></div>

  <div class="brand">
    <span class="brand__mark"></span>
    <span class="brand__name">Bergers<br>Kellnerservice</span>
  </div>
  <p class="brand__tagline">…damit Ihre Gäste bestens versorgt sind!</p>

  <div class="person">
    <h1 class="person__name">Jonas Berger</h1>
    <p class="person__role">Inhaber</p>
  </div>

  <ul class="contact-list">
    <li class="contact-list__item">
      <svg class="contact-list__icon" viewBox="0 0 16 16"><path d="M1 6c0-2 3-3 7-3s7 1 7 3v1h-3V5.5C11 5 9.5 5 8 5s-3 0-4 .5V7H1z"/><path d="M3 8h10l1 6H2z"/></svg>
      02361 482 17 30
    </li>
    <li class="contact-list__item">
      <svg class="contact-list__icon" viewBox="0 0 16 16"><path d="M1 6c0-2 3-3 7-3s7 1 7 3v1h-3V5.5C11 5 9.5 5 8 5s-3 0-4 .5V7H1z"/><path d="M3 8h10l1 6H2z"/></svg>
      0176 284 39 12
    </li>
    <li class="contact-list__item">
      <svg class="contact-list__icon" viewBox="0 0 16 16"><circle cx="8" cy="8" r="7"/><path d="M1 8h14M8 1c-3 3-3 11 0 14M8 1c3 3 3 11 0 14" stroke="#252326" stroke-width="1.2" fill="none"/></svg>
      www.bergers-kellnerservice.de
    </li>
    <li class="contact-list__item">
      <svg class="contact-list__icon" viewBox="0 0 16 16"><rect x="1" y="3" width="14" height="10" rx="1"/><path d="M1.5 3.5 8 9l6.5-5.5" stroke="#252326" stroke-width="1.2" fill="none"/></svg>
      info@bergers-kellnerservice.de
    </li>
    <li class="contact-list__item">
      <svg class="contact-list__icon" viewBox="0 0 16 16"><path d="M8 1a5 5 0 0 0-5 5c0 4 5 9 5 9s5-5 5-9a5 5 0 0 0-5-5zm0 7a2 2 0 1 1 0-4 2 2 0 0 1 0 4z"/></svg>
      Lindenweg 14, 45699 Herten
    </li>
    <li class="contact-list__item">
      <svg class="contact-list__icon" viewBox="0 0 16 16"><rect x="1" y="1" width="14" height="14" rx="2"/></svg>
      social.example/bergerskellnerservice
    </li>
  </ul>
</section>

</body>
</html>
```